Design Startseite Kanzlei-Homepage
Zielgruppe
Wir sind eine Rechtsanwaltskanzlei in Kempten (Allgäu) und regional sowie überregional in verschiedenen Rechtsgebieten tätig. Unsere Zielgruppe sind sowohl private als auch gewerbliche Mandanten.
Aufgabenstellung
Die bestehende Gestaltung wirkt derzeit aus unserer Sicht überholt. Insbesondere soll das bislang dominierende Rot vollständig entfallen.
Stattdessen stellen wir uns ein modernes, hochwertiges Erscheinungsbild vor, primär in dunklen Farbtönen (Anthrazit/Schwarz) kombiniert mit Beige- bzw. warmen Naturtönen. Ziel ist eine klare visuelle Anlehnung an unsere Kanzleiräumlichkeiten (siehe Fotos).
Die Webseite soll insgesamt moderner, klarer und visuell anspruchsvoller wirken, ohne an Seriosität und Zugänglichkeit einzubüßen. Die Balance zwischen hochwertigem Erscheinungsbild und mandantenorientierter Nutzerführung steht für uns im Vordergrund.

```html
<!DOCTYPE html>
<html lang="de">
<head>
<meta charset="utf-8">
<title>Kanzlei – Startseite</title>
<link rel="stylesheet" href="https://fonts.googleapis.com/css2?family=Cinzel:wght@400;500&family=Fira+Sans:wght@400;500&display=swap">
<style>
  :root {
    --page: #ffffff;
    --panel: #f7f7f7;
    --gold: #9a7440;
    --ink: #222222;
    --white: #ffffff;
    --wood-dark: #5a3e26;
    --wood-mid: #9c7a52;
    --wood-light: #d9bf94;
    --stone-dark: #3b2e24;
    --stone-mid: #6e5a48;
    --stone-light: #a38d76;
  }
  * { margin: 0; padding: 0; box-sizing: border-box; }
  html, body { width: 1200px; height: 693px; overflow: hidden; background: var(--page); }
  body { position: relative; font-family: "Fira Sans", Arial, sans-serif; }

  .video-section {
    position: absolute; left: 0; top: 15px; width: 1200px; height: 383px;
  }
  .video-intro {
    position: absolute; left: 0; top: 0; width: 550px; height: 383px; background: var(--panel);
  }
  .video-title {
    position: absolute; left: 120px; top: 124px;
    font-family: "Cinzel", Georgia, serif; font-weight: 400;
    font-size: 19px; letter-spacing: 0.5px; color: var(--gold);
  }
  .video-text {
    position: absolute; left: 116px; top: 155px; width: 316px;
    font-size: 8.6px; line-height: 11px; color: var(--ink);
  }
  .video-media {
    position: absolute; left: 550px; top: 0; width: 650px; height: 383px;
    background:
      radial-gradient(ellipse at 30% 35%, #e0b867 0%, rgba(224,184,103,0) 45%),
      radial-gradient(ellipse at 60% 70%, #3a2418 0%, rgba(58,36,24,0) 40%),
      linear-gradient(180deg, var(--wood-light) 0%, var(--wood-mid) 55%, var(--wood-dark) 100%);
  }
  .play-button {
    position: absolute; left: 840px; top: 176px; width: 48px; height: 48px;
  }

  .reviews-section {
    position: absolute; left: 0; top: 413px; width: 1200px; height: 260px;
    background:
      linear-gradient(rgba(40,30,22,0.35), rgba(40,30,22,0.35)),
      radial-gradient(ellipse at 50% 60%, var(--stone-light) 0%, var(--stone-mid) 45%, var(--stone-dark) 100%);
    text-align: center; color: var(--white);
  }
  .reviews-title {
    position: absolute; left: 0; right: 0; top: 96px;
    font-family: "Cinzel", Georgia, serif; font-weight: 400;
    font-size: 26px; letter-spacing: 0.5px;
  }
  .review-quote {
    position: absolute; left: 312px; width: 562px; top: 140px;
    font-size: 8.6px; line-height: 11px;
  }
  .review-author {
    position: absolute; left: 0; right: 0; top: 192px;
    display: flex; justify-content: center; align-items: center; gap: 16px;
    font-size: 10px; font-weight: 500;
  }
  .review-author::before, .review-author::after {
    content: ""; width: 38px; height: 1px; background: var(--white);
  }
</style>
</head>
<body>
  <section class="video-section">
    <div class="video-intro">
      <h2 class="video-title">Image-Video der Kanzlei</h2>
      <p class="video-text">Sit quodis dendebis moluptam quam nos quodis eum dolorpos quunt et hil ipsae niendi nonsed es ut quossitin pla necta consequi voluptaquat eturis assitia spedicit at aut doloris dia sandit que sin eos aligeni imporem faceper ehenden imeniatur? Lacerunt andisitio. Nam as quatur, iumque ne velessincils dicilsti blaborum excepel id modit exera volupta volupta tiorem acculpa quam, ilitect ibusam, non rest offic to bea eum nihil exerfer speres mod eossum quiasped.</p>
    </div>
    <div class="video-media" role="img" aria-label="Foto: Hausmodell und Richterhammer auf Holztisch"></div>
  </section>

  <svg class="play-button" viewBox="0 0 48 48" aria-label="Video abspielen">
    <circle cx="24" cy="24" r="24" fill="rgba(30,30,30,0.75)"/>
    <path d="M19 14 L35 24 L19 34 Z" fill="none" stroke="#c9a56a" stroke-width="1.6" stroke-linejoin="round"/>
  </svg>

  <section class="reviews-section" role="img" aria-label="Hintergrundfoto: Stuckdecke und Säulen der Kanzleiräume">
    <h2 class="reviews-title">Bewertungen</h2>
    <p class="review-quote">Sit quodis dendebis moluptam quam nos quodis eum dolorpos quunt et hil ipsae niendi nonsed es ut quossitin pla necta. Mmodit exera volupta volupta tiorem acculpa quam, ilitect ibusam, non rest offic to bea eum nihil exerfer speres mod eossum quiasped. modit exera volupta volupta tiorem acculpa quam, ilitect ibusam, non rest offic to bea eum nihil exerfer speres mod eossum quiasped.</p>
    <p class="review-author">Bernhard Lessing</p>
  </section>
</body>
</html>
```